Awesome design needed for standup comedy portal

We need a website designed for a new portal (grinbox.net) dedicated to standup comedy.

- homepage
- featured "hero" content at top
- banner advertising
- browse comics
- browse venues
- search
- signup / login
- social media links

- comic page
- name
- pictures
- calendar of performances
- list of albums (with buy buttons)
- list of specials (Vexora, Plumtrack, etc. with buy buttons)
- reviews
- latest tweets
- latests pixaloop photos
- links to social media accounts
- links to filmdex, podcast

- venue page
- name
- pictures
- address, phone number
- calendar of events
- reviews
- latest tweets
- links to filmdex, podcast

Target Market(s)

Fans of standup comedy and comedians

Number of Pages Required

Font styles to use
Sans Serif

Requirements
Must have
• Will eventually be implemented in bootstrap, so please keep that in mind

```html
<!DOCTYPE html>
<html lang="en">
<head>
<meta charset="utf-8">
<title>Grinbox – Standup Comedy Portal</title>
<link rel="stylesheet" href="https://fonts.googleapis.com/css2?family=Alfa+Slab+One&family=Varela+Round&display=swap">
<style>
  :root{
    --red:#d0202c;
    --red-dark:#b51822;
    --blue:#29a3dc;
    --blue-deep:#1d8fc7;
    --blue-btn:#2b9fd8;
    --white:#ffffff;
    --ink:#2b2b2b;
    --text:#555555;
    --orange:#ef7324;
    --footer:#eeeeef;
    --footer-ink:#4a4a4a;
  }
  *{box-sizing:border-box;margin:0;padding:0}
  html,body{width:700px;height:1200px;overflow:hidden}
  body{position:relative;background:var(--white);font-family:"Varela Round",sans-serif;color:var(--ink)}
  h1,h2,p{font-weight:400}

  /* hero */
  .hero{position:absolute;left:0;top:0;width:700px;height:428px;overflow:hidden}
  .hero-photo{position:absolute;inset:0 0 68px 0;
    background:radial-gradient(ellipse 170px 240px at 350px 250px,#6e6a68 0%,#4d4f57 55%,transparent 100%),
               linear-gradient(180deg,#3f5a86 0%,#5b6f94 45%,#4f5466 75%,#6a5a58 100%)}
  .hero-shade{position:absolute;inset:0;background:rgba(20,30,50,.18)}
  .nav a{position:absolute;color:var(--white);text-decoration:none;font-size:12px;top:44px}
  .nav .home{left:82px;top:38px;width:60px;height:26px;border:2px solid var(--white);text-align:center;line-height:22px}
  .auth{position:absolute;top:0;height:23px;color:var(--white);font-size:11px;line-height:23px;text-align:center}
  .auth.signup{left:520px;width:61px;background:var(--blue-btn)}
  .auth.login{left:581px;width:62px;background:var(--red)}
  .brand{position:absolute;left:300px;top:16px;width:120px;text-align:center}
  .brand-dot{width:50px;height:50px;border-radius:50%;background:var(--red);margin:0 auto 6px}
  .brand-name{color:var(--white);font-size:22px;letter-spacing:1px}
  .hero-title{position:absolute;left:0;width:700px;top:186px;text-align:center;color:var(--white);
    font-family:"Alfa Slab One",serif;font-size:32px;letter-spacing:1px}
  .hero-sub{position:absolute;left:0;width:700px;top:224px;text-align:center;color:var(--white);
    font-family:"Alfa Slab One",serif;font-size:17px}
  .arrow{position:absolute;top:205px}
  .search-band{position:absolute;left:0;top:360px;width:700px;height:68px;background:var(--red)}
  .search-label{position:absolute;top:10px;color:var(--white);font-size:15px}
  .search-box{position:absolute;top:31px;height:24px;background:var(--white);font-size:10px;color:#444;
    padding-left:12px;line-height:24px}
  .search-btn{position:absolute;top:31px;width:25px;height:24px;background:var(--blue-btn);display:flex;align-items:center;justify-content:center}

  /* welcome */
  .welcome-title{position:absolute;left:55px;top:475px;font-size:20px;color:var(--ink)}
  .welcome-text{position:absolute;left:57px;top:508px;width:300px;font-size:9.3px;line-height:17.7px;color:var(--text)}
  .btn-outline-red{position:absolute;left:56px;top:614px;width:89px;height:25px;border:1.5px solid var(--red-dark);
    color:var(--red-dark);font-size:9.5px;text-align:center;line-height:22px}
  .welcome-art{position:absolute;left:358px;top:462px;width:306px;height:172px;
    background:radial-gradient(ellipse at 30% 50%,#e9e9e9,#9b9b9b 70%,transparent 72%),
               radial-gradient(ellipse at 72% 48%,#ececec,#9a9a9a 60%,#ffffff 75%)}

  /* featured */
  .featured{position:absolute;left:0;top:690px;width:700px;height:320px}
  .featured-title{position:absolute;left:0;width:700px;top:712px;text-align:center;color:var(--white);font-size:18px}
  .card-art{position:absolute;top:752px;width:109px;height:129px;border:2px solid var(--white)}
  .card-title{position:absolute;top:889px;width:144px;text-align:center;color:var(--white);font-size:12.5px}
  .card-desc{position:absolute;top:906px;width:144px;text-align:center;color:var(--white);font-size:7.6px;line-height:11.5px}
  .btn-outline-white{position:absolute;top:937px;width:68px;height:20px;border:1.5px solid var(--white);color:var(--white);
    font-size:7.5px;text-align:center;line-height:17px}

  /* ad banner */
  .ad{position:absolute;left:88px;top:1028px;width:530px;height:70px;background:var(--orange)}
  .ad-art{position:absolute;top:10px;width:140px;height:50px;background:rgba(255,255,255,.35)}
  .ad-date{position:absolute;left:0;width:530px;top:9px;text-align:center;color:#222;font-size:8px}
  .ad-name{position:absolute;left:0;width:530px;top:21px;text-align:center;color:#222;font-size:24px}
  .ad-url{position:absolute;left:0;width:530px;top:54px;text-align:center;color:#222;font-size:7px}

  /* footer */
  .footer{position:absolute;left:0;top:1125px;width:700px;height:75px;background:var(--footer)}
  .footer-nav{position:absolute;left:80px;top:22px;font-size:10px;color:var(--footer-ink)}
  .footer-nav span{margin-right:13px}
  .copyright{position:absolute;left:80px;top:42px;font-size:8.5px;color:var(--footer-ink)}
  .social{position:absolute;top:23px;display:flex;align-items:center;gap:3px;font-size:7px;color:var(--footer-ink)}
  .social i{display:block;width:14px;height:14px;border-radius:50%;background:var(--blue-deep)}
</style>
</head>
<body>

<header class="hero">
  <div class="hero-photo" role="img" aria-label="Photo of a comedian performing with a microphone in front of a city window"></div>
  <div class="hero-shade"></div>
  <nav class="nav">
    <a class="home" href="#">Home</a>
    <a href="#" style="left:163px">About Us</a>
    <a href="#" style="left:239px">Comedy</a>
    <a href="#" style="left:457px;top:46px">Venues</a>
    <a href="#" style="left:523px;top:46px">Comics</a>
    <a href="#" style="left:589px;top:46px">Contact</a>
  </nav>
  <a class="auth signup">Sign up</a>
  <a class="auth login">Log In</a>
  <div class="brand"><div class="brand-dot"></div><div class="brand-name">GRINBOX</div></div>
  <h1 class="hero-title">BEST STANDUP COMEDY</h1>
  <p class="hero-sub">MAECENAS ALIQUET VELIT TURPIS</p>
  <svg class="arrow" style="left:40px" width="16" height="26" viewBox="0 0 16 26"><path d="M13 2 3 13l10 11" fill="none" stroke="#fff" stroke-width="3"/></svg>
  <svg class="arrow" style="left:644px" width="16" height="26" viewBox="0 0 16 26"><path d="M3 2l10 11L3 24" fill="none" stroke="#fff" stroke-width="3"/></svg>

  <div class="search-band">
    <div class="search-label" style="left:76px">Browse Comics</div>
    <div class="search-box" style="left:78px;width:244px">Browse comics</div>
    <div class="search-btn" style="left:322px"><svg width="11" height="11" viewBox="0 0 11 11"><circle cx="4.5" cy="4.5" r="3.3" fill="none" stroke="#fff" stroke-width="1.6"/><path d="M7 7l3 3" stroke="#fff" stroke-width="1.8"/></svg></div>
    <div class="search-label" style="left:358px">Browse Venues</div>
    <div class="search-box" style="left:358px;width:243px">Browse Venues</div>
    <div class="search-btn" style="left:601px"><svg width="11" height="11" viewBox="0 0 11 11"><circle cx="4.5" cy="4.5" r="3.3" fill="none" stroke="#fff" stroke-width="1.6"/><path d="M7 7l3 3" stroke="#fff" stroke-width="1.8"/></svg></div>
  </div>
</header>

<section class="welcome">
  <h2 class="welcome-title">Welcome to Our Website</h2>
  <p class="welcome-text">Maecenas aliquet velit turpis Mauris neque metus malesuada nec ultricies sit amet porttitor mattis enim In massa libero interdum nec interdum vel blandit sed nulla In ullamcorper est eget tempor cursus neque mi consectetuer mi a ultricies massa est sed nisl Class aptent taciti sociosqu ad litora torquent per</p>
  <a class="btn-outline-red">LEARN MORE</a>
  <div class="welcome-art" role="img" aria-label="Illustration of two laughing and crying comedy masks in silver"></div>
</section>

<section class="featured-wrap">
  <svg class="featured" width="700" height="320" viewBox="0 0 700 320">
    <path d="M0 0H338l12 14 12-14H700V320Q350 272 0 320Z" fill="var(--blue)"/>
    <line x1="240" y1="34" x2="272" y2="34" stroke="#fff" stroke-width="1"/>
    <circle cx="272" cy="34" r="2" fill="#fff"/>
    <circle cx="430" cy="34" r="2" fill="#fff"/>
    <line x1="430" y1="34" x2="462" y2="34" stroke="#fff" stroke-width="1"/>
  </svg>
  <h2 class="featured-title">Featured Comics</h2>

  <div class="card-art" style="left:83px;background:linear-gradient(135deg,#1a1a1a,#c8202a 60%,#f2d23a)" role="img" aria-label="Pop art comic cover with speech bubbles on black"></div>
  <div class="card-title" style="left:65px">Comic Tittle</div>
  <div class="card-desc" style="left:65px">Maecenas aliquet velit vel turpis<br>Mauris neque metus</div>
  <a class="btn-outline-white" style="left:105px">LEARN MORE</a>

  <div class="card-art" style="left:227px;background:linear-gradient(160deg,#19b6e6,#f0cf48 55%,#e0352f)" role="img" aria-label="Pop art comic cover on cyan background"></div>
  <div class="card-title" style="left:209px">Comic Tittle</div>
  <div class="card-desc" style="left:209px">Maecenas aliquet velit vel turpis<br>Mauris neque metus</div>
  <a class="btn-outline-white" style="left:249px">LEARN MORE</a>

  <div class="card-art" style="left:371px;background:linear-gradient(150deg,#f5e23a,#f0c930 50%,#d93a2c)" role="img" aria-label="Pop art comic cover on yellow dotted background"></div>
  <div class="card-title" style="left:353px">Comic Tittle</div>
  <div class="card-desc" style="left:353px">Maecenas aliquet velit vel turpis<br>Mauris neque metus</div>
  <a class="btn-outline-white" style="left:393px">LEARN MORE</a>

  <div class="card-art" style="left:515px;background:linear-gradient(160deg,#e2342c,#c9262a 60%,#6a3a8c)" role="img" aria-label="Pop art comic cover page on red background"></div>
  <div class="card-title" style="left:497px">Comic Tittle</div>
  <div class="card-desc" style="left:497px">Maecenas aliquet velit vel turpis<br>Mauris neque metus</div>
  <a class="btn-outline-white" style="left:537px">LEARN MORE</a>
</section>

<aside class="ad">
  <div class="ad-art" style="left:8px" role="img" aria-label="Row of figures holding hands"></div>
  <div class="ad-art" style="left:382px" role="img" aria-label="Row of figures holding hands"></div>
  <div class="ad-date">21 MARCH</div>
  <div class="ad-name">UNITY WEEK</div>
  <div class="ad-url">UNITYWEEK.ORG</div>
</aside>

<footer class="footer">
  <nav class="footer-nav"><span>Home</span><span>About Us</span><span>Comedy</span><span>Venues</span><span>Comics</span><span>Contact Us</span></nav>
  <p class="copyright">© 2017 Company Name &nbsp;All right reserved &nbsp;Term of Use</p>
  <div class="social" style="left:470px"><i></i>Chirpr</div>
  <div class="social" style="left:518px"><i></i>Friendlo</div>
  <div class="social" style="left:570px"><i></i>Linkwork</div>
  <div class="social" style="left:626px"><i></i>Circlo</div>
</footer>

</body>
</html>
```